Vibrant, yet professional, stationery set and other designs required.

I need to source a fantastic designer for a new project as part of my company using a new logo designed via sketch harbor.

**UPDATE** I am not looking for just 'fine' design that will suffice. I am looking for something great.

We are a life assurance brokerage based in Dublin, Ireland and BrightRoost.ie is our new website aimed at providing services for young families in Ireland. We are hoping to be the 'Velro' level of service providers in this area and I am looking for the quality of design to reflect this :-) Hopefully that makes sense!

I have a preference for straight lines over curves and waves.

I need...

1. Business card
2. Letterhead
3. Banner (for printing - 76cm X 305cm)
4. Car branding for KORVA 9 (2014 sport model) I believe the templates are freely available online.

Target Market(s)

Parents in Ireland - Aged 27 to 50.

Industry/Entity Type

Financial Planning

Colors

Designer to choose colors to be used in the design.

Requirements
Must have
• All of the items listed in the description above. I like clean, bright, legible, vibrant and professional design.
Should not have
• No silly or 'cheap' looking designs. This is a professional company looking to provide a professional service.

```html
<!DOCTYPE html>
<html lang="en">
<head>
<meta charset="utf-8">
<title>BrightRoost.ie – Stationery and Vehicle Set</title>
<link href="https://fonts.googleapis.com/css2?family=Questrial&family=Roboto+Condensed:wght@400;500&display=swap" rel="stylesheet">
<style>
  :root{
    --bg:#c2c2c2;
    --paper:#ffffff;
    --card:#eeeeee;
    --slate:#7f8c91;
    --slate-light:#95a3a7;
    --ink:#6b7579;
    --ink-soft:#8a9397;
    --accent:#4fa7d3;
    --car:#d9dbdc;
    --car-dark:#b7babc;
  }
  *{box-sizing:border-box;margin:0;padding:0}
  html,body{width:1200px;height:1106px;overflow:hidden;background:var(--bg)}
  body{position:relative;font-family:"Questrial",sans-serif;color:var(--ink)}
  .piece{position:absolute;box-shadow:0 1px 4px rgba(0,0,0,.18)}

  .wordmark{font-family:"Questrial",sans-serif;color:var(--ink);line-height:.9;font-weight:400;letter-spacing:.5px}
  .wordmark span{display:block}
  .wordmark.light{color:#ffffff}

  /* Letterhead */
  .letterhead{left:66px;top:53px;width:506px;height:713px;background:var(--paper)}
  .letterhead .wordmark{position:absolute;left:44px;top:56px;font-size:28px}
  .letterhead .contact{position:absolute;left:355px;top:44px;padding-left:13px;border-left:1px solid #c9cdcf;font-size:7.6px;line-height:10.6px;color:var(--ink-soft);height:72px}
  .letterhead .contact .gap{height:4px}
  .letter-body{position:absolute;left:44px;top:200px;width:421px;font-size:6.6px;line-height:10.9px;color:#7b8488;text-align:justify}
  .letter-body .salutation{font-size:13px;color:var(--ink);margin-bottom:22px}
  .letter-body p{margin-bottom:11px}
  .letter-body .signoff{margin-top:20px}

  /* Business cards */
  .card-front{left:666px;top:54px;width:279px;height:160px;background:var(--card)}
  .card-front .wordmark{position:absolute;left:35px;top:62px;font-size:23px}
  .card-front .details{position:absolute;left:150px;top:39px;padding-left:11px;border-left:1px solid #c9cdcf;font-size:6.6px;line-height:9px;color:var(--ink-soft)}
  .card-front .name{font-family:"Roboto Condensed",sans-serif;font-size:10.5px;color:var(--accent);line-height:11px;font-weight:500}
  .card-front .role{font-family:"Roboto Condensed",sans-serif;font-size:7px;color:var(--ink);margin-bottom:4px}
  .card-front .gap{height:3px}
  .card-back{left:770px;top:254px;width:279px;height:160px;background:var(--slate);display:flex;align-items:center;justify-content:center}
  .card-back .wordmark{font-size:31px}

  /* Banners */
  .banner{left:620px;width:527px;height:131px}
  .banner .wordmark{position:absolute;top:30px;font-size:32px}
  .banner .copy{position:absolute;top:35px;font-family:"Roboto Condensed",sans-serif;font-weight:500;font-size:20px;line-height:24px}
  .banner .points{font-weight:400;font-size:12px;line-height:20px}
  .banner-light{top:462px;background:#f4f4f4}
  .banner-light .wordmark{left:34px}
  .banner-light .copy{right:35px;text-align:right;color:var(--ink-soft)}
  .banner-dark{top:634px;background:var(--slate-light)}
  .banner-dark .wordmark{right:38px;top:30px}
  .banner-dark .copy{left:32px;color:#ffffff}

  /* Vehicle panels */
  .vehicle{position:absolute;top:824px;border-radius:14px;background:linear-gradient(180deg,var(--car) 0%,#eceeef 55%,var(--car-dark) 100%)}
  .vehicle-side{left:48px;width:512px;height:228px}
  .vehicle-front{left:596px;width:264px;height:224px}
  .vehicle-rear{left:900px;width:248px;height:224px}
  .decal{position:absolute;font-family:"Roboto Condensed",sans-serif;color:var(--ink);text-align:center}
  .vehicle-side .wordmark{position:absolute;left:187px;top:104px;font-size:32px}
  .vehicle-front .decal{left:0;right:0;top:76px;font-style:normal}
  .vehicle-front .phone{font-size:15px;font-weight:500}
  .vehicle-front .url{font-size:7.5px}
  .vehicle-rear .decal{left:0;right:0;top:130px;font-size:12px;font-weight:500}
</style>
</head>
<body>

  <section class="piece letterhead">
    <div class="wordmark"><span>bright</span><span>roost.ie</span></div>
    <div class="contact">
      14 Larkfield Row<br>Dublin 6, D06 K2P8
      <div class="gap"></div>
      (P) 01 482 7730<br>(C) 087 315 6642<br>(F) 01 482 7731<br>(E) aidan@brightroost.com<br>(w) www.brightroost.com
    </div>
    <div class="letter-body">
      <div class="salutation">Dear Mr. Keller,</div>
      <p>Lorem ipsum dolor sit amet, consectetur adipiscing elit. Donec orci purus, luctus vitae dignissim eu, iaculis sed purus. Vivamus faucibus, ipsum nec aliquet viverra, leo mauris condimentum ligula, sit amet sagittis enim ligula quis arcu. Nam egestas tortor id nisi porttitor mattis. In tortor ante, ultricies in suscipit a, tempus non massa. Vivamus et auctor mi. Fusce vel massa nulla. Phasellus nec eros mauris, et scelerisque orci.</p>
      <p>Donec malesuada orci vitae nulla accumsan porta a id massa. Quisque accumsan iaculis magna sit amet fringilla. Maecenas consequat, magna eget tincidunt semper, odio nibh rutrum mi, id feugiat ante nisi eu risus. Vestibulum nunc orci, rhoncus a placerat in, ultricies in mi. Cras mattis varius eros, vel fringilla nisi suscipit eget. Quisque scelerisque sagittis nulla at porttitor.</p>
      <p>Sed id augue vitae urna euismod commodo aliquet a quam. Pellentesque arcu velit, cursus et malesuada ut, consequat et diam. Nullam erat sem, rhoncus id ullamcorper vitae, rhoncus et arcu. In ultricies ultricies nulla, ut rutrum nisi iaculis at. Donec eu magna a metus ornare faucibus. Fusce aliquet faucibus ultricies. Morbi semper, est id tincidunt gravida, sem arcu adipiscing lacus, ac bibendum nulla leo eu purus. Quisque nec diam sed risus consectetur a accumsan quis quis nibh. Vestibulum id purus lorem.</p>
      <p>It is a long established fact that a reader will be distracted by the readable content of a page when looking at its layout. The point of using Lorem Ipsum is that it has a more-or-less normal distribution of letters, as opposed to using 'Content here, content here', making it look like readable English. Many desktop publishing packages</p>
      <div class="signoff">Sincerely,</div>
    </div>
  </section>

  <section class="piece card-front">
    <div class="wordmark"><span>bright</span><span>roost.ie</span></div>
    <div class="details">
      <div class="name">AIDAN KELLER</div>
      <div class="role">CEO/FOUNDER</div>
      14 Larkfield Row<br>Dublin 6, D06 K2P8
      <div class="gap"></div>
      (P) 01 482 7730<br>(C) 087 315 6642<br>(F) 01 482 7731<br>(E) aidan@brightroost.com<br>(w) www.brightroost.com
    </div>
  </section>

  <section class="piece card-back">
    <div class="wordmark light"><span>bright</span><span>roost.ie</span></div>
  </section>

  <section class="piece banner banner-light">
    <div class="wordmark"><span>bright</span><span>roost.ie</span></div>
    <div class="copy">YOUR TAGLINE HERE<br>WWW.BRIGHTROOST.COM<div class="points">point • Point • Point • Point</div></div>
  </section>

  <section class="piece banner banner-dark">
    <div class="copy">YOUR TAGLINE HERE<br>WWW.BRIGHTROOST.COM<div class="points">point • Point • Point • Point</div></div>
    <div class="wordmark light"><span>bright</span><span>roost.ie</span></div>
  </section>

  <section class="vehicle vehicle-side" role="img" aria-label="White KORVA 9 hatchback, side view, with BrightRoost.ie name on the door">
    <div class="wordmark"><span>bright</span><span>roost.ie</span></div>
  </section>

  <section class="vehicle vehicle-front" role="img" aria-label="White KORVA 9 hatchback, front view, with phone number and web address on the bonnet">
    <div class="decal"><div class="phone">01 482 7730</div><div class="url">WWW.BRIGHTROOST.COM</div></div>
  </section>

  <section class="vehicle vehicle-rear" role="img" aria-label="White KORVA 9 hatchback, rear view, with web address on the tailgate">
    <div class="decal">WWW.BRIGHTROOST.COM</div>
  </section>

</body>
</html>
```